New Business Card Design Project

Use the flyer uploaded and website www.brightoakbuilders.com for inspiration.
List Our Services on Backside of business cards
Marcus Delling
Harborline Builders Inc.
Licensed General Contractors
858-471-6093

Contact Information for Business Card

Use the flyer uploaded and website www.brightoakbuilders.com for inspiration. List Our Services on Backside of business cards Marcus Delling Harborline Builders Inc. Licensed General Contractors 858-471-6093

```html
<!DOCTYPE html>
<html lang="en">
<head>
<meta charset="utf-8">
<title>Harborline Builders – Business Cards</title>
<link href="https://fonts.googleapis.com/css2?family=Bebas+Neue&family=Roboto:wght@400&display=swap" rel="stylesheet">
<style>
  :root{
    --stage:#e6e7ea;
    --ink:#121212;
    --paper:#ffffff;
    --accent-blue:#3183c8;
    --accent-red:#e3161d;
    --text:#1d1d1d;
  }
  *{margin:0;padding:0;box-sizing:border-box}
  html,body{width:1200px;height:1200px;overflow:hidden;background:var(--stage)}
  .stage{position:relative;width:1200px;height:1200px}
  .card{position:absolute;top:303px;width:368px;height:594px;background:var(--paper);overflow:hidden;
        font-family:"Roboto",Arial,sans-serif;color:var(--text)}
  .card--back{left:201px}
  .card--front{left:599px}
  .card__art{position:absolute;inset:0;width:368px;height:594px}
  .brand-name{position:absolute;top:94px;left:0;width:272px;text-align:center;
              color:var(--paper);font-size:18px;letter-spacing:1.5px;text-transform:uppercase;font-weight:400}
  .guarantee{position:absolute;left:25px;top:328px;font-family:"Bebas Neue",Impact,sans-serif;
             font-size:23.5px;color:var(--accent-red);letter-spacing:0.1px;white-space:nowrap}
  .specialty-tag{position:absolute;left:25px;top:355px;height:31px;line-height:33px;padding-left:4px;
                 font-family:"Bebas Neue",Impact,sans-serif;font-size:23px;color:var(--paper)}
  .service-list{position:absolute;left:25px;top:397px;list-style:none}
  .service-list li{position:relative;padding-left:16px;font-size:15px;line-height:18.7px;white-space:nowrap}
  .service-list li::before{content:"";position:absolute;left:2px;top:6px;width:7px;height:7px;border-radius:50%;background:var(--accent-red)}
  .person-name{position:absolute;left:24px;top:374px;font-family:"Bebas Neue",Impact,sans-serif;
               font-size:43px;color:var(--accent-red);letter-spacing:-0.3px}
  .contact-list{position:absolute;left:24px;top:436px;list-style:none}
  .contact-list li{display:flex;align-items:center;height:21.7px;font-size:17px;white-space:nowrap}
  .contact-list svg{width:16px;height:16px;margin-right:10px;flex:none}
  .company-lines{position:absolute;left:33px;top:524px;color:var(--accent-red);font-size:16.5px;line-height:21.5px;white-space:nowrap}
</style>
</head>
<body>
<div class="stage">

  <!-- Back side: services -->
  <section class="card card--back">
    <svg class="card__art" viewBox="0 0 368 594" aria-hidden="false">
      <defs>
        <linearGradient id="kitchenTones" x1="0" y1="1" x2="1" y2="0">
          <stop offset="0" stop-color="#8a6a35"/>
          <stop offset="0.35" stop-color="#cfa15d"/>
          <stop offset="0.55" stop-color="#d9cfc1"/>
          <stop offset="0.75" stop-color="#f0eeea"/>
          <stop offset="1" stop-color="#e2dfdb"/>
        </linearGradient>
      </defs>
      <polygon points="0,150 368,90 368,325 0,287" fill="url(#kitchenTones)" role="img" aria-label="Photo of a renovated kitchen blending into a sketch of the same kitchen"/>
      <polygon points="0,0 368,0 368,119 0,236" fill="var(--ink)"/>
      <polyline points="27,320 27,209 313,114 313,562 197,562" fill="none" stroke="var(--accent-blue)" stroke-width="2"/>
      <polygon points="26,355 185,355 173,386 26,386" fill="var(--accent-blue)"/>
    </svg>
    <div class="brand-name">Harborline Builders</div>
    <h2 class="guarantee">Our Services Are 100% Guarenteed</h2>
    <div class="specialty-tag">Specializing In</div>
    <ul class="service-list">
      <li>Remodel: Kitchen &amp; Bath</li>
      <li>Painting: Interior &amp; Exterior</li>
      <li>Flooring: Carpet, Vinyl, Wood</li>
      <li>Window &amp; Door Replacement</li>
      <li>Plumbing: Repairs &amp; Upgrades</li>
      <li>Energy-Efficient Upgrades</li>
      <li>Deck &amp; Patio Construction</li>
      <li>Water &amp; Mold Damage</li>
      <li>Garage Renovation</li>
    </ul>
  </section>

  <!-- Front side: contact -->
  <section class="card card--front">
    <svg class="card__art" viewBox="0 0 368 594">
      <defs>
        <linearGradient id="bathTones" x1="0" y1="0" x2="1" y2="1">
          <stop offset="0" stop-color="#cfd8da"/>
          <stop offset="0.4" stop-color="#eef0ef"/>
          <stop offset="0.75" stop-color="#e3e4e2"/>
          <stop offset="1" stop-color="#d2d3d1"/>
        </linearGradient>
      </defs>
      <polygon points="0,150 368,90 368,368 0,330" fill="url(#bathTones)" role="img" aria-label="Photo of a bright white bathroom with vanity and glass shower"/>
      <polygon points="0,0 368,0 368,121 0,236" fill="var(--ink)"/>
      <polyline points="27,374 27,209 313,114 313,551 277,551" fill="none" stroke="var(--accent-blue)" stroke-width="2"/>
    </svg>
    <div class="brand-name">Harborline Builders</div>
    <h1 class="person-name">Marcus Delling</h1>
    <ul class="contact-list">
      <li>
        <svg viewBox="0 0 16 16"><path d="M4 1.5l2.2 3-1.3 1.6c.8 1.8 2.2 3.2 4 4l1.6-1.3 3 2.2-1.2 2.6C6.9 13.2 2.8 9.1 1.4 3.7z" fill="none" stroke="var(--accent-blue)" stroke-width="1.4" stroke-linejoin="round"/></svg>
        858-471-6093
      </li>
      <li>
        <svg viewBox="0 0 16 16"><rect x="1" y="3.5" width="14" height="9.5" fill="var(--accent-blue)"/><path d="M1 3.5l7 5.5 7-5.5" fill="none" stroke="#fff" stroke-width="1.2"/></svg>
        info@harborlinebuilders.com
      </li>
      <li>
        <svg viewBox="0 0 16 16"><g fill="none" stroke="var(--accent-blue)" stroke-width="1.3"><circle cx="8" cy="8" r="6.5"/><ellipse cx="8" cy="8" rx="2.8" ry="6.5"/><path d="M1.5 8h13M2.5 4.8h11M2.5 11.2h11"/></g></svg>
        BrightOakBuilders.com
      </li>
    </ul>
    <p class="company-lines">Harborline Builders Inc.<br>Licensed General Contractors</p>
  </section>

</div>
</body>
</html>
```